Bright bears day nursery qrp limited

we would like create a website that can be updated by us easily as we have regular changes to what we provide and need. we would like something that is classy but also appealing from a child's aspect. we would be looking to add our own logo and our kinderwatch logo both attached, if you guys can create it and we will work with the preferred choice to add all the text.
We would like the links to family pathways, kinderwatch report and our chatterbook feed on the front page

we are looking for a website for our childcare business we have 2 nurseries that we would like one website.
showing our opening hours, price list, policies etc as well as photos, description of our day, staff photos and their training accreditation's.

Target Market(s)

Families

Industry/Entity Type

Childcare

Number of Pages Required

5+ page

Font styles to use
Serif

Colors

Designer to choose colors to be used in the design.

Requirements
Must have
• links to social media and other websites, photographs, links to download registration forms etc, parents able to leave reviews. google maps link, job opportunities
Nice to have
• facilities to take payments

```html
<!DOCTYPE html>
<html lang="en">
<head>
<meta charset="utf-8">
<title>Bright Bears Day Nursery</title>
<link href="https://fonts.googleapis.com/css2?family=Play:wght@400;700&family=Raleway:wght@400;500;600;700&family=Tinos:wght@700&display=swap" rel="stylesheet">
<style>
:root{
  --navy:#0f2a6b;
  --pink:#d42a72;
  --green:#45a83a;
  --lime:#8dc63f;
  --dark:#333333;
  --grey-band:#ececec;
  --text:#222;
  --white:#fff;
  --gold:#f3b21b;
}
*{box-sizing:border-box;margin:0;padding:0}
html,body{width:1200px;height:3098px;overflow:hidden}
body{font-family:"Raleway",sans-serif;color:var(--text);background:var(--white)}
section,header,footer{position:relative;width:1200px}
h2{font-family:"Play",sans-serif;font-weight:700;font-size:33px;color:var(--navy);text-align:center}
.rule{width:46px;height:3px;background:var(--pink);margin:12px auto 0}

/* header */
.site-header{height:138px}
.brand{position:absolute;top:18px;display:flex;align-items:center;gap:10px;font-family:"Play",sans-serif;font-weight:700;font-size:22px;color:var(--navy);line-height:1.05;width:150px}
.brand-mark{width:26px;height:26px;background:var(--pink);flex:none}
.brand.one{left:162px}.brand.two{left:322px}
.top-actions{position:absolute;top:20px;right:190px;display:flex;gap:14px}
.pill{font-size:13px;font-weight:600;color:var(--white);padding:6px 12px;border-radius:2px}
.pill.loc{background:#555}.pill.enroll{background:var(--green)}
.phone{position:absolute;top:16px;right:170px;transform:translateX(100%);display:flex;align-items:center;gap:8px;font-family:"Play",sans-serif;font-size:22px;color:var(--navy)}
.phone svg{width:24px;height:24px}
.main-nav{position:absolute;top:104px;left:540px;display:flex;font-size:14px;font-weight:600;color:var(--navy)}
.main-nav a{padding:0 20px;border-left:1px solid #bbb}
.main-nav a:first-child{border:none;color:var(--pink)}

/* hero */
.hero{height:482px;background:linear-gradient(180deg,#c9cfd2 0%,#e3e1dc 35%,#b7b0a6 70%,#8a8f77 100%)}
.hero .arrow{position:absolute;top:230px;width:28px;height:28px;background:rgba(0,0,0,.7);color:#fff;display:flex;align-items:center;justify-content:center;font-size:16px}
.hero .arrow.l{left:6px}.hero .arrow.r{right:6px}
.hero-caption{position:absolute;bottom:0;left:0;right:0;height:36px;background:rgba(0,0,0,.6);color:#fff;font-family:"Play",sans-serif;font-size:24px;text-align:center;line-height:36px}

/* welcome */
.welcome{height:295px;padding-top:40px;text-align:center}
.welcome .lead{font-size:14px;margin:20px 0 10px}
.welcome .body{font-size:11px;line-height:18px;width:1060px;margin:0 auto}
.btn-dark{display:inline-block;margin-top:22px;background:var(--dark);color:#fff;font-size:14px;padding:9px 28px}

/* programs */
.programs{height:458px;background:linear-gradient(135deg,#6d5e62,#4a4548 50%,#5e5a5f);padding-top:32px}
.programs h2{color:#fff}
.program-list{display:flex;justify-content:center;gap:50px;margin-top:40px}
.program{width:178px;text-align:center;color:#fff}
.program .photo{width:178px;height:178px;border-radius:50%;border:7px solid rgba(200,200,200,.75);background:radial-gradient(circle,#f1d3c0,#b98e7a)}
.program h3{font-family:"Play",sans-serif;font-size:19px;margin-top:12px}
.program .age{font-size:12px;font-weight:700;margin:6px 0}
.program p{font-size:12px;line-height:16px}
.c-pink{color:var(--pink)}.c-lime{color:var(--lime)}

/* why choose */
.why{height:403px;padding-top:42px;text-align:center}
.why .intro{font-size:12px;font-weight:600;line-height:18px;width:880px;margin:22px auto 0}
.features{display:flex;justify-content:center;gap:70px;margin-top:32px}
.feature{width:162px}
.feature .icon{width:100px;height:100px;border-radius:50%;border:2px solid var(--navy);margin:0 auto;display:flex;align-items:center;justify-content:center}
.feature .icon svg{width:54px;height:54px}
.feature h3{font-size:13px;font-weight:700;margin:20px 0 16px}
.feature p{font-size:11px;line-height:16px}
.feature .more{font-size:10px;margin-top:3px}

/* reviews */
.reviews{height:384px;background:var(--grey-band);padding-top:38px;text-align:center}
.quote{width:880px;margin:30px auto 0;font-size:11px;font-style:italic;line-height:18px;position:relative}
.avatar{width:78px;height:78px;border-radius:50%;border:3px solid #e67c2a;background:linear-gradient(#c4ccd6,#7a8594);margin:22px auto 0}
.reviewer{font-family:"Tinos",serif;font-weight:700;color:#e67c2a;font-size:16px;margin-top:6px}
.stars{color:var(--gold);font-size:13px;letter-spacing:2px}
.dots{display:flex;gap:6px;justify-content:center;margin-top:6px}
.dots span{width:12px;height:12px;border-radius:50%;border:1px solid #aaa}
.dots span+span{background:#aaa}

/* gallery */
.gallery{height:256px;padding-top:38px}
.thumbs{display:flex;justify-content:center;gap:18px;margin-top:32px;position:relative}
.thumb{width:165px;height:105px;border:3px solid #fff;box-shadow:0 0 4px rgba(0,0,0,.35);background:linear-gradient(135deg,#e8c79f,#c05a40 60%,#5b8ed0)}
.thumb.g2{background:linear-gradient(135deg,#4b4d52,#2e2f33);display:flex;align-items:center;justify-content:center;color:#fff;font-size:13px;text-align:center;padding:0 18px}
.thumb.g3{background:linear-gradient(135deg,#bfe0a3,#5e9d48)}
.thumb.g4{background:linear-gradient(135deg,#eed7be,#5f8fc7)}
.thumb.g5{background:linear-gradient(135deg,#f2d0b1,#a56b47)}
.g-arrow{position:absolute;top:38px;font-size:26px;color:#111}
.g-arrow.l{left:136px}.g-arrow.r{right:136px}

/* contact */
.contact{height:599px;background:linear-gradient(180deg,#3a352f 0%,#55463b 45%,#6b5d4b 100%);padding-top:44px;color:#fff}
.contact h2{color:#fff}
.contact .rule{background:#fff}
.info{display:flex;justify-content:center;gap:40px;margin-top:30px;text-align:center}
.info div{width:210px}
.info svg{width:26px;height:26px;fill:#fff}
.info h3{font-size:14px;font-weight:600;margin:8px 0 6px}
.info p{font-size:12px;font-weight:600;line-height:16px}
.form-panel{position:absolute;left:182px;top:244px;width:840px;height:298px;background:rgba(180,180,180,.45);padding:14px 0 0 56px}
.form-panel .title{width:586px;text-align:center;font-size:17px;font-weight:600}
.form-panel .sub{width:586px;text-align:center;font-size:19px;font-weight:700;margin-top:6px}
.fields{display:grid;grid-template-columns:283px 283px;gap:13px 20px;margin-top:16px;width:586px}
.field{height:33px;background:rgba(255,255,255,.2);border:1px solid rgba(255,255,255,.45);font-size:11px;padding:9px 10px}
.field.wide{grid-column:1/3;height:74px}
.submit{grid-column:1/3;height:32px;background:var(--green);text-align:center;font-weight:700;font-size:14px;line-height:32px}
.badge{position:absolute;left:696px;width:118px;height:118px;background:#1d2e7c;border-radius:4px}
.badge.a{top:20px}.badge.b{top:152px;border-right:24px solid var(--gold)}

/* footer */
.site-footer{height:83px;background:var(--navy);color:#fff}
.foot-nav{position:absolute;left:168px;top:22px;display:flex;font-size:12px;font-weight:600}
.foot-nav a{padding:0 16px;border-left:1px solid #8899cc}
.foot-nav a:first-child{border:none}
.copy{position:absolute;left:162px;top:58px;font-size:10px}
.fees{position:absolute;right:172px;top:10px;font-size:12px}
.follow{position:absolute;right:172px;top:42px;display:flex;align-items:center;gap:6px;font-size:12px}
.follow span.c{width:26px;height:26px;border-radius:50%;border:2px solid #fff}
a{color:inherit;text-decoration:none}
</style>
</head>
<body>

<header class="site-header">
  <div class="brand one"><span class="brand-mark"></span>Bright Bears</div>
  <div class="brand two">Bright Bears Day Nursery</div>
  <div class="top-actions">
    <a class="pill loc" href="#">Our Location »</a>
    <a class="pill enroll" href="#">Enroll Now »</a>
  </div>
  <div class="phone">
    <svg viewBox="0 0 24 24"><circle cx="12" cy="12" r="11" fill="none" stroke="#d42a72" stroke-width="1.5"/><path d="M8 6l2 3-1 1.5c.8 1.8 2 3 3.5 3.5L14 13l3 2-1 2.5C11 17 7 13 6.5 8z" fill="#d42a72"/></svg>
    123-456-7890
  </div>
  <nav class="main-nav">
    <a href="#">Home</a><a href="#">About Us</a><a href="#">Our Services</a><a href="#">Price</a><a href="#">Gallery</a><a href="#">Contact Us</a>
  </nav>
</header>

<section class="hero" role="img" aria-label="Bright nursery playroom with toys, tables and children's artwork on the wall">
  <span class="arrow l">‹</span><span class="arrow r">›</span>
  <div class="hero-caption">Day Nurseries Providing Full Day Care For Children In The UK</div>
</section>

<section class="welcome">
  <h2>Welcome to Bright Bears Day Nursery</h2>
  <div class="rule"></div>
  <p class="lead">Duis autem vel eum iriure dolor in hendrerit in vulputate velit esse molestie consequat, vel illum dolore.</p>
  <p class="body">Lorem ipsum dolor sit amet, consectetuer adipiscing elit, sed diam nonummy nibh euismod tincidunt ut laoreet dolore magna aliquam erat volutpat. Ut wisi enim ad minim veniam, quis nostrud exerci tation ullamcorper suscipit lobortis nisl ut aliquip ex ea commodo consequat. Duis autem vel eum iriure dolor in hendrerit in vulputate velit esse molestie consequat, vel illum dolore eu feugiat nulla facilisis at vero eros et accumsan et iusto odio dignissim qui blandit praesent luptatum zzril delenit augue duis dolore te feugait nulla facilisi.</p>
  <a class="btn-dark" href="#">Read More</a>
</section>

<section class="programs" role="img" aria-label="Children playing together, shown darkened behind the programs">
  <h2>Our Programs</h2>
  <div class="rule"></div>
  <div class="program-list">
    <div class="program"><div class="photo" role="img" aria-label="Infants playing"></div><h3 class="c-pink">Infant</h3><p class="age">Age 6 Weeks - 18 Months</p><p>Lorem ipsum dolor sit amet, tuer adipiscing elit ed diam.</p></div>
    <div class="program"><div class="photo" role="img" aria-label="Toddler stacking toys"></div><h3 class="c-lime">Toddler</h3><p class="age">Age 18 -36 Months</p><p>Lorem ipsum dolor sit amet, tuer adipiscing elit ed diam.</p></div>
    <div class="program"><div class="photo" role="img" aria-label="Pre-school child at a table"></div><h3 class="c-pink">Pre-School</h3><p class="age">Age 3-5 Years</p><p>Lorem ipsum dolor sit amet, tuer adipiscing elit ed diam.</p></div>
    <div class="program"><div class="photo" role="img" aria-label="Kindergarten classroom"></div><h3 class="c-lime">Kindergarten</h3><p class="age">Kindergarten-12 years</p><p>Lorem ipsum dolor sit amet, tuer adipiscing elit ed diam.</p></div>
  </div>
</section>

<section class="why">
  <h2>Why Choose Us</h2>
  <div class="rule"></div>
  <p class="intro">Lorem ipsum dolor sit amet, consectetuer adipiscing elit, sed diam nonummy nibh euismod tincidunt ut laoreet dolore magna aliquam erat volutpat. Ut wisi enim ad minim veniam, quis nostrud exerci tation ullamcorper suscipit.</p>
  <div class="features">
    <div class="feature"><div class="icon"><svg viewBox="0 0 54 54" fill="none" stroke="#111" stroke-width="3"><circle cx="20" cy="18" r="10"/><path d="M27 25l16 16"/><circle cx="45" cy="43" r="4" fill="#111"/></svg></div><h3>Fun Leaning</h3><p>Lorem ipsum dolor sit amet sit amet ipsum dolor sit amet, dolor sit amet...</p><p class="more">[+]</p></div>
    <div class="feature"><div class="icon"><svg viewBox="0 0 54 54" fill="none" stroke="#111" stroke-width="3"><rect x="10" y="8" width="28" height="38" rx="2"/><path d="M17 18h14M17 26h14M17 34h8"/><circle cx="40" cy="40" r="9" fill="#111"/><path d="M36 40l3 3 5-6" stroke="#fff"/></svg></div><h3>Easy Academics</h3><p>Lorem ipsum dolor sit amet sit amet ipsum dolor sit amet, dolor sit amet...</p><p class="more">[+]</p></div>
    <div class="feature"><div class="icon"><svg viewBox="0 0 54 54" fill="none" stroke="#111" stroke-width="3"><path d="M27 12a11 11 0 0 0-6 20v6h12v-6a11 11 0 0 0-6-20z"/><path d="M22 43h10M27 4v3M12 12l2 2M42 12l-2 2"/></svg></div><h3>Innovative Approach</h3><p>Lorem ipsum dolor sit amet sit amet ipsum dolor sit amet, dolor sit amet...</p><p class="more">[+]</p></div>
    <div class="feature"><div class="icon"><svg viewBox="0 0 54 54" fill="#111"><circle cx="14" cy="12" r="5"/><rect x="9" y="19" width="10" height="16"/><rect x="10" y="35" width="3" height="13"/><rect x="15" y="35" width="3" height="13"/><rect x="24" y="8" width="26" height="20" fill="none" stroke="#111" stroke-width="3"/><path d="M18 22l10-6" stroke="#111" stroke-width="3"/></svg></div><h3>Qualified Staff</h3><p>Lorem ipsum dolor sit amet sit amet ipsum dolor sit amet, dolor sit amet...</p><p class="more">[+]</p></div>
  </div>
</section>

<section class="reviews">
  <h2>Parent Reveiws</h2>
  <div class="rule"></div>
  <p class="quote">“ Lorem ipsum sit amet co adipisctised udml esil mol monk dtepor incidunt ut la dolore ma aliquamni kn nibhmi enim nim veni exercitation ullamco ips sdltnol am conoplk adipiscig elitsedmi do euismod te epo uom accuil dollarmjk oremque laantium. Accusant dolorernquen more consec moptnonumy! facilea Lorem ipsum sit amet co adipisctised udml esil mol monk dtepor incidunt ut la dolore ma aliquamni kn nibhmi enim nim veni exercitation ullamco ips sdltnol am conoplk adipiscig elitsedmi do euismod te epo uom accuil dollarmjk oremque laudantium. Accusant ”</p>
  <div class="avatar" role="img" aria-label="Reviewing parent portrait"></div>
  <p class="reviewer">- Maya Fenwick</p>
  <p class="stars">★★★★</p>
  <div class="dots"><span></span><span></span></div>
</section>

<section class="gallery">
  <h2>Photo Gallery</h2>
  <div class="rule"></div>
  <div class="thumbs">
    <span class="g-arrow l">‹</span>
    <div class="thumb" role="img" aria-label="Children painting at a table"></div>
    <div class="thumb g2">Lorem Ispum is the dummy text</div>
    <div class="thumb g3" role="img" aria-label="Children playing outdoors"></div>
    <div class="thumb g4" role="img" aria-label="Children at a classroom table"></div>
    <div class="thumb g5" role="img" aria-label="Children reading together"></div>
    <span class="g-arrow r">›</span>
  </div>
</section>

<section class="contact" role="img" aria-label="Nursery building and garden play area at dusk">
  <h2>Contact Us</h2>
  <div class="rule"></div>
  <div class="info">
    <div><svg viewBox="0 0 24 24"><path d="M12 2a7 7 0 0 0-7 7c0 5 7 13 7 13s7-8 7-13a7 7 0 0 0-7-7zm0 10a3 3 0 1 1 0-6 3 3 0 0 1 0 6z"/></svg><h3>Location</h3><p>Street Name, City Name<br>State Zipcode</p></div>
    <div><svg viewBox="0 0 24 24"><path d="M2 5h20v14H2z"/><path d="M2 5l10 8 10-8" fill="none" stroke="#555" stroke-width="1.5"/></svg><h3>Email</h3><p>inquiry@brightbearsnursery.com</p></div>
    <div><svg viewBox="0 0 24 24"><path d="M6 2l4 5-2 2.5c1.3 3 3.5 5.2 6.5 6.5L17 14l5 4-2 4C11 21 3 13 2 4z"/></svg><h3>Call</h3><p>123-456-7890</p></div>
    <div><svg viewBox="0 0 24 24" fill="none" stroke="#fff" stroke-width="2"><circle cx="12" cy="12" r="9"/><path d="M12 7v5l3 3"/></svg><h3>Timing</h3><p>Mon. To Sat.: 10.00 a.m. to - 04.00 p.m.<br>Sunday : Close</p></div>
  </div>
  <div class="form-panel">
    <p class="title">Get In Touch</p>
    <p class="sub">Have Qustions ? Well be happy To Answes!</p>
    <div class="fields">
      <div class="field">Name</div><div class="field">Email</div>
      <div class="field">Inquiry for class</div><div class="field">Phone</div>
      <div class="field wide">Inquiry message</div>
      <div class="submit">SUBMIT</div>
    </div>
    <div class="badge a" role="img" aria-label="Kinderwatch outstanding rating badge"></div>
    <div class="badge b" role="img" aria-label="Kinderwatch outstanding early years provider badge"></div>
  </div>
</section>

<footer class="site-footer">
  <nav class="foot-nav"><a href="#">Home</a><a href="#">About Us</a><a href="#">Our Services</a><a href="#">Price</a><a href="#">Gallery</a><a href="#">Contact Us</a></nav>
  <p class="copy">Copyright © 2017 Bright Bears Nursery School All Rights Reserved.</p>
  <p class="fees">Pay Your Fees Here</p>
  <div class="follow">Follow Us <span class="c" aria-label="Chatterbook"></span><span class="c"></span><span class="c"></span><span class="c"></span></div>
</footer>

</body>
</html>
```